Realty Group Needs Classy, Contemporary Letterhead Design

We need a letterhead design for a new realty company located in NY, USA. We buy investment properties to rehabilitate and or keep in our rental portfolio.

```html
<!DOCTYPE html>
<html lang="en">
<head>
<meta charset="utf-8">
<title>Meridian Realty Group Letterhead</title>
<link rel="stylesheet" href="https://fonts.googleapis.com/css2?family=Open+Sans:wght@400;600&family=Lato:wght@400;700&display=swap">
<style>
  :root {
    --purple: #4b2a8c;
    --grey-band: #808080;
    --ink: #3a3a3a;
    --ink-soft: #555555;
    --rule: #9a9a9a;
    --backdrop: #e9e9e9;
    --paper: #ffffff;
  }
  * { margin: 0; padding: 0; box-sizing: border-box; }
  html, body { width: 1040px; height: 1200px; overflow: hidden; background: var(--backdrop); }
  .letterhead {
    position: absolute; left: 80px; top: 34px;
    width: 881px; height: 1133px;
    background: var(--paper);
    box-shadow: 0 2px 10px rgba(0,0,0,0.18);
    font-family: "Open Sans", sans-serif; color: var(--ink);
  }
  .band { position: absolute; left: 0; width: 881px; height: 19px; display: block; }
  .band--top { top: 0; }
  .band--bottom { bottom: 0; }
  .brand {
    position: absolute; top: 64px; left: 0; width: 100%;
    display: flex; justify-content: center; align-items: center; gap: 12px;
  }
  .brand__mark { width: 18px; height: 18px; background: var(--purple); }
  .brand__name {
    font-family: "Open Sans", sans-serif; font-weight: 600;
    font-size: 26px; line-height: 32px; color: var(--purple);
  }
  .letter { position: absolute; left: 84px; width: 711px; font-size: 13.6px; }
  .letter p { line-height: 25.3px; text-align: justify; }
  .issue-date { top: 210px; }
  .recipient { top: 241px; line-height: 17px; }
  .salutation { top: 341px; }
  .body-copy { top: 391px; letter-spacing: -0.1px; }
  .body-copy p + p { margin-top: 25.3px; }
  .closing { top: 774px; }
  .signature {
    position: absolute; left: 84px; top: 812px; width: 200px; height: 22px;
    border-radius: 11px; background: linear-gradient(90deg, #d6d6d6, #eeeeee);
  }
  .signatory { position: absolute; left: 84px; top: 848px; }
  .signatory__name { font-size: 17.5px; font-weight: 600; color: #333; line-height: 24px; }
  .signatory__title { font-size: 13.6px; color: var(--ink-soft); line-height: 24px; }
  .footer {
    position: absolute; left: 180px; width: 520px; top: 1060px;
    font-family: "Lato", sans-serif; font-size: 16.5px; color: #222; text-align: center;
  }
  .footer__address { padding-bottom: 3px; border-bottom: 1.5px solid var(--rule); line-height: 22px; }
  .footer__contact { line-height: 26px; }
  .footer__label { color: var(--purple); font-weight: 700; }
  .footer__web { color: var(--purple); }
</style>
</head>
<body>
<main class="letterhead">
  <svg class="band band--top" viewBox="0 0 881 19" aria-hidden="true">
    <polygon points="0,0 437,0 418,19 0,19" fill="var(--purple)"/>
    <polygon points="450,0 881,0 881,19 431,19" fill="var(--grey-band)"/>
  </svg>

  <header class="brand">
    <span class="brand__mark" aria-hidden="true"></span>
    <span class="brand__name">Meridian Realty Group, LLC</span>
  </header>

  <div class="letter issue-date">Issuing Date: May 5, 2018</div>
  <div class="letter recipient">
    Name Of Employee Mr. XYZABC<br>
    Address of Employee<br>
    Address Line 2 etc..
  </div>
  <div class="letter salutation">Dear Mr.XYZABC</div>

  <div class="letter body-copy">
    <p>Lorem Ipsum has been the industry's standard dummy text ever since the 1500s, when an unknown printer took a galley of type and scrambled it to make a type specimen book. It has survived not only five centuries, but also the leap into electronic typesetting, remaining essentially unchanged. It was popularised in the 1960s with the release of Letraset sheets containing Lorem Ipsum passages, and more recently with desktop publishing software like Aldus PageMaker including versions of Lorem Ipsum.</p>
    <p>Lorem Ipsum is simply dummy text of the printing and typesetting industry. Lorem Ipsum has been the industry's standard dummy text ever since the 1500s, when an unknown printer took a galley of type and scrambled it to make a type specimen book.</p>
    <p>It has survived not only five centuries, but also the leap into electronic typesetting, remaining essentially unchanged. It was popularised in the 1960s with the release of Letraset sheets containing Lorem IpsumIpsum passages.</p>
  </div>

  <div class="letter closing">Yours Sincerely</div>
  <div class="signature" role="img" aria-label="Handwritten signature of Daniel Hartwell"></div>
  <div class="signatory">
    <div class="signatory__name">Daniel Hartwell</div>
    <div class="signatory__title">Managing Director</div>
  </div>

  <footer class="footer">
    <div class="footer__address">421, Address line goes here Country Name, 45452</div>
    <div class="footer__contact">
      <span class="footer__label">P:</span> 044-555 218 406 | <span class="footer__label">E:</span> info@meridianrg.com | <span class="footer__web">www.meridianrg.com</span>
    </div>
  </footer>

  <svg class="band band--bottom" viewBox="0 0 881 19" aria-hidden="true">
    <polygon points="0,0 438,0 420,19 0,19" fill="var(--purple)"/>
    <polygon points="452,0 881,0 881,19 434,19" fill="var(--grey-band)"/>
  </svg>
</main>
</body>
</html>
```